Business Card for Graphic Design Firm

This project is for a new graphic design firm based in New Jersey called Velmoria. We outsource graphic design and marketing jobs. We want to communicate that this is a professional company but it as well creative and artistic. This card may be used as a horizontal double sided paper card or a vertical single sided translucent card so feel free to submit designs in whichever format or both.
Updates

Reason: Extending the deadline because I'm not exactly satisfied with the designs so far.

Please view the updated project brief

Target Market(s)

Adults aged 25-60

Industry/Entity Type

Graphic Design

Font styles to use
Serif
Sans Serif

Requirements
Nice to have
• Maybe a triangular pattern around the edges similar to our logo

```html
<!DOCTYPE html>
<html lang="en">
<head>
<meta charset="utf-8">
<title>Velmoria business card</title>
<link href="https://fonts.googleapis.com/css2?family=Open+Sans:wght@400;600;700&display=swap" rel="stylesheet">
<style>
  :root {
    --page: #e9e6e1;
    --paper: #ffffff;
    --teal: #1a9fb8;
    --teal-deep: #13879e;
    --amber: #f2ad17;
    --amber-light: #f6c13c;
    --ink-light: #ffffff;
    --slate: #7e8a90;
  }
  html, body {
    margin: 0;
    width: 1200px;
    height: 1023px;
    overflow: hidden;
    background: var(--page);
    font-family: "Open Sans", sans-serif;
  }
  .card {
    position: absolute;
    left: 250px;
    width: 700px;
    height: 400px;
    background: var(--paper);
    box-shadow: 0 10px 26px rgba(0,0,0,.18);
    overflow: hidden;
  }
  .card--front { top: 90px; }
  .card--back { top: 533px; }
  .card__shapes { position: absolute; inset: 0; }
  .holder {
    position: absolute;
    left: 40px;
    top: 26px;
    color: var(--ink-light);
  }
  .holder__name { font-size: 19px; font-weight: 600; margin: 0; }
  .holder__role { font-size: 13px; color: var(--amber-light); margin: 2px 0 0; }
  .brand {
    position: absolute;
    display: flex;
    align-items: center;
    gap: 12px;
    font-weight: 700;
    letter-spacing: 3px;
    line-height: 1;
    color: var(--teal-deep);
    white-space: nowrap;
  }
  .brand__mark { width: 16px; height: 16px; background: var(--amber); }
  .card--front .brand { right: 40px; top: 128px; font-size: 34px; }
  .card--back .brand {
    left: 50%;
    bottom: 40px;
    transform: translateX(-50%);
    font-size: 44px;
    color: var(--slate);
  }
  .card--back .brand__mark { width: 20px; height: 20px; }
  .contact {
    position: absolute;
    left: 340px;
    top: 258px;
    margin: 0;
    padding: 0;
    list-style: none;
    color: var(--ink-light);
    font-size: 14px;
  }
  .contact__item { display: flex; align-items: flex-start; gap: 12px; margin-bottom: 12px; line-height: 1.3; }
  .contact__icon { flex: none; width: 24px; height: 22px; }
</style>
</head>
<body>

<section class="card card--front">
  <svg class="card__shapes" viewBox="0 0 700 400" aria-hidden="true">
    <polygon points="0,0 520,0 350,180 0,60" fill="var(--teal)"/>
    <polygon points="350,180 700,250 700,400 200,400" fill="var(--teal-deep)"/>
  </svg>
  <div class="holder">
    <p class="holder__name">Lukas Brenner</p>
    <p class="holder__role">Hybrid Clouds</p>
  </div>
  <div class="brand"><span class="brand__mark"></span>VELMORIA</div>
  <ul class="contact">
    <li class="contact__item">
      <svg class="contact__icon" viewBox="0 0 24 22"><polygon points="2,20 12,2 22,20" fill="none" stroke="#fff" stroke-width="2"/><rect x="9.5" y="10" width="5" height="8" rx="1" fill="var(--amber)"/></svg>
      <span>+41 78 000 12 34</span>
    </li>
    <li class="contact__item">
      <svg class="contact__icon" viewBox="0 0 24 22"><polygon points="2,20 12,2 22,20" fill="none" stroke="#fff" stroke-width="2"/><rect x="8" y="11" width="8" height="6" fill="var(--amber)"/></svg>
      <span>lukas@velmoria.ch</span>
    </li>
    <li class="contact__item">
      <svg class="contact__icon" viewBox="0 0 24 22"><polygon points="2,20 12,2 22,20" fill="none" stroke="#fff" stroke-width="2"/><polygon points="12,9 7,13 8,13 8,18 16,18 16,13 17,13" fill="var(--amber)"/></svg>
      <span>Lindenweg 12 8000 Sampleton<br>Switzerland</span>
    </li>
  </ul>
</section>

<section class="card card--back">
  <svg class="card__shapes" viewBox="0 0 700 400" aria-hidden="true">
    <polygon points="0,0 0,400 340,200" fill="var(--amber)"/>
    <polygon points="700,0 700,400 360,200" fill="var(--amber-light)"/>
  </svg>
  <div class="brand"><span class="brand__mark"></span>VELMORIA</div>
</section>

</body>
</html>
```